Homemaking training schools needs a Business Card design

Designer, Hello!

No special requirements, good-looking enough.
--------------------------------------------------------------------------

Name: Marcus Dole
Chairman
Tel: 0574-71948263
Mobile: 13857420916
Email: kelvora@mailnest.example
Web: www.prt2019.example
Add: No.258, LanpingJie, BeiyuanQu, Ningbo, Zhejiang

LOGO
Ningbo PRT Homemaking Training School

Target Market(s)

pregnant women, mothers, infants, the elderly and families, including cleaning, cooking, nursing training.

Industry/Entity Type

Business

Contact Information for Business Card

Name: Marcus Dole
Chairman
Tel: 0574-71948263
Mobile: 13857420916
Email: kelvora@mailnest.example
Web: www.prt2019.example

LOGO

Font styles to use
Serif
Sans Serif
Decorative

Requirements
Nice to have
• Feels: clean, specifications, safety, comfort, warmth and happiness.

```html
<!DOCTYPE html>
<html lang="en">
<head>
<meta charset="utf-8">
<title>PRT Homemaking Training – Business Card</title>
<link href="https://fonts.googleapis.com/css2?family=Montserrat:ital,wght@0,500;0,700;1,400&family=Quicksand:wght@300;400;500;700&display=swap" rel="stylesheet">
<style>
  :root {
    --bg: #e9eaec;
    --card: #ffffff;
    --blue: #5f86c2;
    --blue-soft: #8ea7d3;
    --pink: #e05a9c;
    --grey: #6f7072;
    --rule: #8a8b8d;
  }
  * { margin: 0; padding: 0; box-sizing: border-box; }
  html, body { width: 1200px; height: 720px; overflow: hidden; background: var(--bg); }
  .canvas { position: relative; width: 1200px; height: 720px; }

  .card {
    position: absolute; top: 205px; width: 510px; height: 300px;
    background: var(--card);
    box-shadow: 0 3px 10px rgba(0,0,0,.08);
  }
  .card--back { left: 50px; }
  .card--front { left: 640px; }

  /* two-tone accent rule */
  .accent { position: absolute; height: 3px; width: 120px; display: flex; }
  .accent span { flex: 1; }
  .accent--top { top: 34px; left: 150px; }
  .accent--top span:first-child { background: var(--blue-soft); }
  .accent--top span:last-child { background: var(--pink); }
  .accent--bottom { top: 262px; left: 190px; width: 130px; }
  .accent--bottom span:first-child { background: var(--pink); }
  .accent--bottom span:last-child { background: var(--blue); }

  .holder { position: absolute; top: 46px; left: 40px; width: 300px; text-align: center; }
  .holder__name {
    font-family: "Montserrat", sans-serif; font-weight: 700;
    font-size: 29px; letter-spacing: .5px; color: var(--blue-soft);
  }
  .holder__title {
    font-family: "Montserrat", sans-serif; font-style: italic; font-weight: 400;
    font-size: 10px; letter-spacing: 1px; color: var(--blue-soft); margin-top: 1px;
  }

  .address {
    position: absolute; top: 104px; left: 60px; width: 330px;
    font-family: "Montserrat", sans-serif; font-weight: 700; font-style: normal;
    font-size: 14.5px; line-height: 1.5; color: var(--grey); text-align: center;
  }

  .contacts { position: absolute; top: 160px; left: 26px; right: 30px; list-style: none; }
  .contact { display: flex; align-items: center; height: 30px; }
  .contact__icon {
    width: 24px; height: 20px; background: var(--blue); flex: none;
    display: flex; align-items: center; justify-content: center; margin-right: 12px;
    position: relative;
  }
  .contact__icon::before {
    content: ""; position: absolute; right: 100%; top: 50%;
    width: 8px; height: 1px; background: var(--rule);
  }
  .contact__text {
    font-family: "Quicksand", sans-serif; font-weight: 500;
    font-size: 17px; color: var(--blue); white-space: nowrap;
  }
  .contact__rule {
    flex: 1; height: 1px; background: var(--rule); margin-left: 10px; position: relative;
  }
  .contact__rule::after {
    content: ""; position: absolute; right: 0; top: -5px; width: 1px; height: 11px; background: var(--rule);
  }

  .brand {
    position: absolute; left: 60px; right: 50px; top: 110px;
    display: flex; flex-direction: column; align-items: flex-end;
  }
  .brand__name {
    font-family: "Quicksand", sans-serif; font-weight: 700;
    font-size: 50px; line-height: 1; color: var(--grey); letter-spacing: .5px;
  }
  .brand__tagline {
    display: flex; align-items: center; gap: 10px; width: 100%; margin-top: 10px;
    font-family: "Quicksand", sans-serif; font-weight: 400;
    font-size: 21px; color: var(--grey); white-space: nowrap;
  }
  .brand__tagline::before,
  .brand__tagline::after {
    content: ""; flex: 1; height: 1.5px; background: var(--rule);
  }
</style>
</head>
<body>
<main class="canvas">

  <section class="card card--back" aria-label="Business card, contact side">
    <div class="accent accent--top"><span></span><span></span></div>
    <header class="holder">
      <h1 class="holder__name">MARCUS DOLE</h1>
      <p class="holder__title">CHAIRMAN</p>
    </header>
    <address class="address">
      No. 258, LanpingJie, BeiyuanQu<br>Ningbo, Zhejiang
    </address>
    <ul class="contacts">
      <li class="contact">
        <span class="contact__icon">
          <svg width="10" height="14" viewBox="0 0 10 14"><rect x="1" y="0.8" width="8" height="12.4" rx="1.4" fill="none" stroke="#fff" stroke-width="1.2"/><circle cx="5" cy="11" r=".8" fill="#fff"/></svg>
        </span>
        <span class="contact__text">0574 71948263 | 138 5742 0916</span>
        <span class="contact__rule"></span>
      </li>
      <li class="contact">
        <span class="contact__icon">
          <svg width="14" height="10" viewBox="0 0 14 10"><rect x=".6" y=".6" width="12.8" height="8.8" fill="none" stroke="#fff" stroke-width="1.2"/><path d="M.6 .6 7 5.6 13.4 .6" fill="none" stroke="#fff" stroke-width="1.2"/></svg>
        </span>
        <span class="contact__text">kelvora@mailnest.example</span>
        <span class="contact__rule"></span>
      </li>
      <li class="contact">
        <span class="contact__icon">
          <svg width="13" height="13" viewBox="0 0 14 14"><circle cx="7" cy="7" r="5.8" fill="none" stroke="#fff" stroke-width="1.2"/><ellipse cx="7" cy="7" rx="2.6" ry="5.8" fill="none" stroke="#fff" stroke-width="1"/><path d="M1.2 7h11.6" stroke="#fff" stroke-width="1"/></svg>
        </span>
        <span class="contact__text">www.prt2019.example</span>
        <span class="contact__rule"></span>
      </li>
    </ul>
    <div class="accent accent--bottom"><span></span><span></span></div>
  </section>

  <section class="card card--front" aria-label="Business card, brand side">
    <div class="brand">
      <span class="brand__name">Pei RuoTang</span>
      <span class="brand__tagline">Training &amp; Services</span>
    </div>
  </section>

</main>
</body>
</html>
```